Site for entrepreneurs/small businesses needs Logo, Homepage

Looking for a logo, either an icon, or stylized text, or a combination of both, and a home page design which fits with it. The logo will be for use on the public website as well as for printed collateral (business cards, post cards, brochures and various other marketing materials).

The site is called Orbitwell (Orbitwell.example). This is to be a national, and eventually an international brand. The new service will provide an easy-to-use platform for entrepreneurs to build their business and web presence together in an integrated way which allows them to focus on their core competency.

The site/service will be dead-simple to use, A/B/C, 1/2/3. We will want some sort of "Get started for FREE" promotional space to collect the person's email address with multiple points of interest which guide the user back to this one call to action: sign up for free. We will feature editorial/blog stories, customer testimonials, and present several key features the the reader just can't live without if they are starting a new business.

Criteria:
* Refer to our comparable sites/logos in the design document attached
* Incorporate our color scheme (but complementary colors welcome)
* No Serif fonts!
* No photo-realistic elements for logo
* Logo must present well in gray scale and/or black/white (for printed materials)
* Strokes/borders that are wider to promote simplicity (vs. thin/precise lines which promote technical complexity)

Inspirations:
* Creative/Custom (but legible) fonts
* Excitement, energetic, jumping for joy
* Karate / Ninja / Power / Precision
* Dance Moves
* Regional influences: California, Silicon Valley, West Coast, Surf City, Beaches, Sunset
* Simple/easy, no-brainer solutions

Target Market(s)

Small Businesses / Entrepreneurs

Logo Text

Orbitwell or Orbitwell.example

Number of Pages Required

1 page

Font styles to use
Sans Serif
Decorative

Requirements
Must have
• See the attached style guide (PDF)

```html
<!DOCTYPE html>
<html lang="en">
<head>
<meta charset="utf-8">
<title>Orbitwell – Home</title>
<link href="https://fonts.googleapis.com/css2?family=Montserrat:wght@400;500;600;700&family=Open+Sans:wght@400;600&display=swap" rel="stylesheet">
<style>
:root{
  --orange:#f7880f;
  --navy:#0b1a7a;
  --navy-deep:#06105a;
  --blue-title:#1d4a8c;
  --ink:#333;
  --text:#666;
  --light:#f4f4f4;
  --white:#fff;
}
*{box-sizing:border-box;margin:0;padding:0}
html,body{width:1200px;height:2848px;overflow:hidden}
body{position:relative;background:var(--white);font-family:"Open Sans",sans-serif;color:var(--text)}
.abs{position:absolute}
h1,h2,h3,.brand,.nav a,.btn{font-family:"Montserrat",sans-serif}

/* hero */
.hero{position:absolute;left:0;top:0;width:1200px;height:691px;background:var(--light);overflow:hidden}
.hero-wave{position:absolute;left:0;top:0}
.hero-art{position:absolute;left:650px;top:150px;width:500px;height:480px;border-radius:20px;
  background:radial-gradient(circle at 70% 60%,#2ab4ff 0,#1b4fd8 30%,rgba(11,26,122,0) 70%)}
.brand{display:flex;align-items:center;gap:12px;font-weight:700;font-size:30px;color:var(--orange)}
.brand .dot{width:34px;height:34px;border-radius:50%;background:var(--orange)}
.site-header .brand{position:absolute;left:86px;top:44px}
.nav a{position:absolute;top:55px;font-size:12px;font-weight:600;color:#222;text-decoration:none;white-space:nowrap}
.nav a.on-dark{color:var(--white)}
.btn-cta{position:absolute;left:922px;top:40px;width:190px;height:44px;border-radius:22px;background:var(--orange);color:var(--white);
  font-family:"Montserrat",sans-serif;font-size:11.5px;font-weight:600;display:flex;align-items:center;justify-content:center}
.hero h1{left:81px;top:236px;font-size:31px;font-weight:600;color:var(--orange)}
.hero .lead{left:86px;top:298px;width:420px;font-size:11.5px;line-height:26px;color:var(--ink)}
.field{position:absolute;left:86px;width:398px;height:46px;border:1px solid #ccc;background:var(--white);
  font-size:12px;color:#444;padding:14px 16px}
.btn{background:var(--orange);color:var(--white);font-size:13px;font-weight:500;display:flex;align-items:center;justify-content:center}
.hero .btn{position:absolute;left:86px;top:514px;width:117px;height:40px}

/* section headings */
.sec-title{position:absolute;left:0;width:1200px;text-align:center;font-size:25px;font-weight:500;color:#333}
.sec-lead{position:absolute;left:230px;width:740px;text-align:center;font-size:11.5px;line-height:26px;color:var(--text)}
.sec-lead.one-line{left:150px;width:900px}

/* features */
.feature-art{position:absolute;width:292px;height:292px;border-radius:50%;border:8px solid #e8e8e8;
  background:radial-gradient(circle,#fff 0,#fdf3e6 55%,#fff 75%)}
.feature h3{position:absolute;font-size:17px;font-weight:600;color:var(--orange)}
.feature p{position:absolute;width:460px;font-size:11.5px;line-height:27.5px;color:var(--text);text-align:justify}
.btn-outline{position:absolute;width:120px;height:40px;border:1.5px solid var(--orange);color:var(--orange);
  font-family:"Montserrat",sans-serif;font-size:12px;font-weight:500;display:flex;align-items:center;justify-content:center}

/* testimonials */
.testimonials{position:absolute;left:0;top:1624px;width:1200px;height:479px;background:linear-gradient(135deg,#f8901a,#f17d06)}
.testimonials .sec-title{color:var(--white);top:48px}
.testimonials .sec-lead{color:var(--white);top:96px}
.quote-card{position:absolute;top:154px;width:325px;height:190px;background:rgba(255,255,255,.14);border:1px solid rgba(160,70,0,.35);padding:20px 26px}
.stars{color:var(--white);font-size:15px;letter-spacing:1px;font-weight:700;margin-bottom:12px}
.quote-card p{font-size:11.5px;line-height:24px;color:var(--white)}
.author{position:absolute;top:366px;display:flex;align-items:center;gap:18px}
.avatar{width:68px;height:68px;border-radius:50%;border:3px solid #fff;background:linear-gradient(#c9a27f,#7a5a3f)}
.author b{display:block;font-family:"Montserrat",sans-serif;font-size:13.5px;font-weight:600;color:var(--white)}
.author span{font-size:11.5px;color:var(--white)}

/* blog */
.post{position:absolute;top:2232px;width:329px}
.post-img{position:relative;width:329px;height:224px;background:linear-gradient(135deg,#1f4f8c,#8fb4d6)}
.date{position:absolute;left:14px;top:14px;width:64px;height:68px;background:var(--orange);color:var(--white);text-align:center;font-family:"Montserrat",sans-serif}
.date b{display:block;font-size:27px;font-weight:500;line-height:40px}
.date span{font-size:11px}
.post h3{margin-top:20px;font-size:15.5px;font-weight:600;color:var(--blue-title)}
.post p{margin-top:20px;font-size:11.5px;line-height:26px;color:var(--text)}

/* footer */
.site-footer{position:absolute;left:0;top:2641px;width:1200px;height:207px;background:linear-gradient(90deg,var(--navy-deep),#102a9a 60%,var(--navy-deep))}
.site-footer .brand{position:absolute;left:99px;top:72px;color:var(--white);font-size:36px}
.site-footer .brand .dot{background:var(--white)}
.foot-nav{position:absolute;left:425px;top:67px;display:flex;font-family:"Montserrat",sans-serif;font-size:12px;color:var(--white)}
.foot-nav span{margin-right:22px}
.foot-nav i{font-style:normal;margin-right:22px}
.copy{position:absolute;left:425px;top:124px;font-size:11.5px;color:#d8def5}
.social{position:absolute;left:920px;top:118px;display:flex;gap:8px}
.social span{width:28px;height:28px;border-radius:50%;border:1.5px solid var(--white)}
</style>
</head>
<body>

<section class="hero">
  <svg class="hero-wave" width="1200" height="691" viewBox="0 0 1200 691" aria-hidden="true">
    <path d="M770,0 C870,35 850,100 740,160 C620,230 630,330 560,420 C500,500 450,600 420,691 L1200,691 L1200,0 Z" fill="var(--orange)"/>
    <path d="M800,0 C900,40 880,105 770,165 C655,235 665,335 595,425 C535,505 480,600 460,691 L1200,691 L1200,0 Z" fill="var(--navy)"/>
  </svg>
  <div class="hero-art" role="img" aria-label="Illustration of a person working on holographic dashboards beside a launching rocket"></div>

  <header class="site-header">
    <div class="brand"><span class="dot"></span>Orbitwell</div>
    <nav class="nav">
      <a style="left:353px">HOME</a>
      <a style="left:429px">ABOUT US</a>
      <a style="left:530px">FEATURES</a>
      <a style="left:630px">BLOG</a>
      <a style="left:700px">TESTIMONIALS</a>
      <a class="on-dark" style="left:826px">CONTCAT US</a>
    </nav>
    <div class="btn-cta">GET STARTED FOR FREE</div>
  </header>

  <h1 class="abs">GET STARTED FOR FREE</h1>
  <p class="abs lead">Sed ut perspiciatis unde omnis iste natus error sit voluptatem accusantium doloremque laudantium, totam rem aperiam, eaque ipsa quae ab illo inve-narchitecto beatae vitae dicta sunt explicabo.</p>
  <div class="field" style="top:394px">Enter Your Email :</div>
  <div class="field" style="top:449px">Password :</div>
  <div class="btn">SIGN UP</div>
</section>

<section class="features">
  <h2 class="sec-title" style="top:738px">KEY FEATURES</h2>
  <p class="sec-lead" style="top:782px">Sed ut perspiciatis unde omnis iste natus error sit voluptatem accusantium doloremque laudantium, totam rem aperiam, eaque ipsa quae ab illo inventore veritatis et quasi architecto beatae vitae dicta sunt explicabo.</p>

  <div class="feature">
    <div class="feature-art" style="left:192px;top:895px" role="img" aria-label="Line illustration of a light bulb with a globe and gears"></div>
    <h3 style="left:549px;top:912px">SED UT PERSPICIATIS UNDE OMNIS</h3>
    <p style="left:551px;top:958px">Sed ut perspiciatis unde omnis iste natus error sit voluptatem accusantium dolorem que laudantium, totam rem aperiam, eaque ipsa quae ab illo inventore veritatis et quasi architecto beatae vitae dicta sunt explicabo. Nemo enim ipsam voluptatem quia volup-tas sit aspernatur aut odit aut fugit, sed quia consequuntur magni dolores eos qui ratione voluptatem sequi nesciunt.</p>
    <div class="btn-outline" style="left:551px;top:1120px">READ MORE</div>
  </div>

  <div class="feature">
    <h3 style="left:196px;top:1279px">SED UT PERSPICIATIS UNDE OMNIS</h3>
    <p style="left:198px;top:1325px">Sed ut perspiciatis unde omnis iste natus error sit voluptatem accusantium dolorem que laudantium, totam rem aperiam, eaque ipsa quae ab illo inventore veritatis et quasi architecto beatae vitae dicta sunt explicabo. Nemo enim ipsam voluptatem quia volup-tas sit aspernatur aut odit aut fugit, sed quia consequuntur magni dolores eos qui ratione voluptatem sequi nesciunt.</p>
    <div class="btn-outline" style="left:198px;top:1487px">READ MORE</div>
    <div class="feature-art" style="left:722px;top:1262px" role="img" aria-label="Line illustration of hands typing on a laptop with charts, gears and mail"></div>
  </div>
</section>

<section class="testimonials">
  <h2 class="sec-title">CUSTOMER TESTIMONIALS</h2>
  <p class="sec-lead one-line">Sed ut perspiciatis unde omnis iste natus error sit voluptatem accusantium doloremque laudantium, totam rem aperiam, eaque ipsa</p>

  <div class="quote-card" style="left:86px"><div class="stars">“ ★★★★★</div><p>Sed ut perspiciatis unde omnis iste natus error sit voluptatem accusantium doloremque laudantium, totam rem aperiam, eaque ipsa quae ab illo inven tore veritatis et quasi architecto beatae vitae dicta sunt explicabo.</p></div>
  <div class="quote-card" style="left:437px"><div class="stars">“ ★★★★★</div><p>Sed ut perspiciatis unde omnis iste natus error sit voluptatem accusantium doloremque laudantium, totam rem aperiam, eaque ipsa quae ab illo inven tore veritatis et quasi architecto beatae vitae dicta sunt explicabo.</p></div>
  <div class="quote-card" style="left:789px"><div class="stars">“ ★★★★★</div><p>Sed ut perspiciatis unde omnis iste natus error sit voluptatem accusantium doloremque laudantium, totam rem aperiam, eaque ipsa quae ab illo inven tore veritatis et quasi architecto beatae vitae dicta sunt explicabo.</p></div>

  <div class="author" style="left:94px"><div class="avatar" role="img" aria-label="Customer portrait"></div><div><b>DANA REYES</b><span>Posed on 28-Apr 2018</span></div></div>
  <div class="author" style="left:446px"><div class="avatar" role="img" aria-label="Customer portrait"></div><div><b>DANA REYES</b><span>Posed on 28-Apr 2018</span></div></div>
  <div class="author" style="left:797px"><div class="avatar" role="img" aria-label="Customer portrait"></div><div><b>DANA REYES</b><span>Posed on 28-Apr 2018</span></div></div>
</section>

<section class="blog">
  <h2 class="sec-title" style="top:2134px">LATEST BLOG</h2>
  <p class="sec-lead one-line" style="top:2178px">Sed ut perspiciatis unde omnis iste natus error sit voluptatem accusantium doloremque laudantium, totam rem aperiam, eaque ipsa</p>

  <article class="post" style="left:86px">
    <div class="post-img" role="img" aria-label="Photo of a laptop with glowing network graphics"><div class="date"><b>24</b><span>MAY</span></div></div>
    <h3>SED UT PERSPICIATIS UNDE</h3>
    <p>Sed ut perspiciatis unde omnis iste natus error sit volu ptat em accusantium doloremque laudantium, totam rem periam, unde omnis iste natus error eaque ipsa</p>
  </article>
  <article class="post" style="left:436px">
    <div class="post-img" style="background:linear-gradient(135deg,#0d1f3c,#3d7ab8)" role="img" aria-label="Photo of a hand touching a rising business chart"><div class="date"><b>24</b><span>MAY</span></div></div>
    <h3>SED UT PERSPICIATIS UNDE</h3>
    <p>Sed ut perspiciatis unde omnis iste natus error sit volu ptat em accusantium doloremque laudantium, totam rem periam, unde omnis iste natus error eaque ipsa</p>
  </article>
  <article class="post" style="left:785px">
    <div class="post-img" style="background:linear-gradient(135deg,#d9d4cc,#8e8a84)" role="img" aria-label="Photo of hands working at a laptop with printed reports"><div class="date"><b>24</b><span>MAY</span></div></div>
    <h3>SED UT PERSPICIATIS UNDE</h3>
    <p>Sed ut perspiciatis unde omnis iste natus error sit volu ptat em accusantium doloremque laudantium, totam rem periam, unde omnis iste natus error eaque ipsa</p>
  </article>
</section>

<footer class="site-footer">
  <div class="brand"><span class="dot"></span>Orbitwell</div>
  <nav class="foot-nav">
    <span>HOME</span><i>|</i><span>ABOUT US</span><i>|</i><span>FEATURES</span><i>|</i><span>BLOG</span><i>|</i><span>TESTIMONIALS</span><i>|</i><span>CONTACT US</span>
  </nav>
  <p class="copy">© Copyright-2018 Orbitwell.All rights reserved.</p>
  <div class="social" aria-label="Social links"><span></span><span></span><span></span><span></span><span></span></div>
</footer>

</body>
</html>
```